Yogurt product needs a simple yet striking packaging.

We need a packaging for our yogurt product based in Singapore and Malaysia that is to be retailed in supermarkets. The brand of the yogurt is called péng which means cow in mandarin. The details of our yogurt is as follows: Indian style all natural yogurt, plain in flavor. Its consistency is thick and creamy. It is preservative free and sugar free. We would like to see simple yet striking designs.

The packaging would be printed on a 200ml plastic cup (silk screen printing). The dimension for the cup is 235mm (w) x 69mm (h).

UPDATE:
We would be selecting 2 designs (First place and Second place) for this contest

Target Market(s)

Consumers who purchase yogurt.

Industry/Entity Type

Product

Requirements
Must have
• We would require some form of an artwork/picture that depicts a plain yogurt. It could be on a spoon, in a bowl, or a close up just on its own.
• UPDATED:
• The following texts are needed to be displayed on the package:
• 1. 'Indian style all natural yogurt' (Indian style could be subtle while all natural yogurt is highlighted as the main text).
• 2. 'Plain' (The flavor of the yogurt).
• 3. 'No Preservatives' and 'No Sugar Added' (Additional description about the yogurt).
• 4. The 2 certifications attached in the brief (Halal and Ravok).
• 5. 'Ingredients: Water, milk solids, live and active cultures' (Ingredients for the yogurt).
• 6. 'Refrigerate below 4°C', 'Do not accept if seal is broken' and '200ml' (Additional contents required in the packaging).
• 7. Nutritional information, place of manufacture and product bar code which are attached in this brief.
Nice to have
• We would like the designers to have the freedom to create designs to their interest and ability, although we really love the designs from yogurt brands like Velumar and Tobbe's.

```html
<!DOCTYPE html>
<html lang="en">
<head>
<meta charset="utf-8">
<title>Plain Indian Style All Natural Yogurt – Cup Label</title>
<link rel="stylesheet" href="https://fonts.googleapis.com/css2?family=Libre+Caslon+Text:wght@400&family=Crimson+Text:wght@400;600&family=Sacramento&display=swap">
<style>
  :root {
    --paper: #ffffff;
    --ink: #1f1f1f;
    --ink-soft: #3a3a3a;
    --berry: #c23a55;
    --berry-deep: #a8203f;
    --berry-light: #e5a3b2;
  }
  * { margin: 0; padding: 0; box-sizing: border-box; }
  html, body {
    width: 1200px;
    height: 1200px;
    overflow: hidden;
    background: var(--paper);
  }
  .label {
    position: relative;
    width: 1200px;
    height: 1200px;
    color: var(--ink);
    text-align: center;
  }
  .flavour {
    position: absolute;
    top: 300px;
    left: 0;
    width: 100%;
    font-family: "Crimson Text", serif;
    font-size: 34px;
    letter-spacing: 6px;
    color: var(--ink-soft);
  }
  .style-line {
    position: absolute;
    top: 340px;
    left: 0;
    width: 100%;
    font-family: "Sacramento", cursive;
    font-size: 104px;
    line-height: 1;
    color: var(--berry);
  }
  .product-name {
    position: absolute;
    top: 455px;
    left: 0;
    width: 100%;
    font-family: "Libre Caslon Text", serif;
    font-weight: 400;
    line-height: 1.02;
    font-size: 104px;
    color: var(--ink);
  }
  .claim {
    position: absolute;
    top: 480px;
    font-family: "Crimson Text", serif;
    font-size: 46px;
    line-height: 1;
    color: var(--ink);
  }
  .claim-left {
    right: 920px;
    text-align: right;
    padding-right: 28px;
    border-right: 2px solid var(--ink-soft);
  }
  .claim-right {
    left: 885px;
    text-align: left;
    padding-left: 24px;
    border-left: 2px solid var(--ink-soft);
    width: 260px;
  }
  .claim span { display: block; padding: 6px 0; }
  .subclaim {
    position: absolute;
    top: 752px;
    left: 0;
    width: 100%;
    font-family: "Crimson Text", serif;
    font-weight: 600;
    font-size: 40px;
    color: var(--ink);
  }
  .lotus-art {
    position: absolute;
    top: 820px;
    left: 330px;
    width: 540px;
    height: 240px;
  }
</style>
</head>
<body>
  <main class="label">
    <p class="flavour">PLAIN</p>
    <p class="style-line">Indian Style</p>

    <p class="claim claim-left"><span>Sugar</span><span>free</span></p>
    <h1 class="product-name">All Natural<br>Yogurt</h1>
    <p class="claim claim-right"><span>Thick and</span><span>Creamy</span></p>

    <p class="subclaim">Preservative-free</p>

    <svg class="lotus-art" viewBox="0 0 540 240" role="img" aria-label="Watercolour lotus flower illustration with scattered berry-coloured dots">
      <defs>
        <radialGradient id="lotusTone" cx="50%" cy="75%" r="60%">
          <stop offset="0%" stop-color="var(--berry-deep)"/>
          <stop offset="60%" stop-color="var(--berry)"/>
          <stop offset="100%" stop-color="var(--berry-light)" stop-opacity="0"/>
        </radialGradient>
      </defs>
      <ellipse cx="270" cy="200" rx="260" ry="180" fill="url(#lotusTone)"/>
    </svg>
  </main>
</body>
</html>
```